Kelumo.cn needs pages to be re-designed

www.kelumo.cn is our current new site which was launched in April.
We're a financial services website in the crowdfunding space in China to connect borrower's and lender's.

test.kelumo.cn is our test site
u: test
p: newtest
http://test.kelumo.cn/
http://test.kelumo.cn/user/accounts/new_lender
http://test.kelumo.cn/user/accounts/new_borrower
http://test.kelumo.cn/introductions/protection
http://test.kelumo.cn/introductions
http://test.kelumo.cn/introductions/kelumo_admin
http://test.kelumo.cn/introductions/contact
Some of the pages have pop-ups in the bloc's of the pages. Please click the links, to see more content.

User's currently criticize the website for being:
- Too Western looking
- Too simple, too little content
- Content NOT in the pop-ups are too simple
- Pictures are too big and too much blank space
- Relevant information is not there when needed
- The pictures are too generic

What we would like to do is re-design those pages with the same color scheme and style to be more compelling, efficient, non-intimidating and easy-to-use. Our audience is Ages 25-35 predominantly male investors.
We are looking for more ideas to make the content match the style, while bridging western and chinese design. Our ultimate goal is to increase registrants to the website and highlight our core competitive advantages.

Some competitors websites are:
www.fobuxiqi.com
www.tamev.com
www.zzzlendo.com

Reason: Not enough good designs that follow the prompt. Same style, better information layout!

Reason: Still have not received a design we're satisfied with

Reason: WE DONT WANT A COMPLETE REDESIGN OF PAGES . KEEP THE EXACT SAME COLOR AND STYLE - WE WANT CONTENT RE-DESIGN! THE BLOCS ARE TOO SIMPLE - WE WANT MORE CONTENT INSIDE.

Reason: no new designs

Reason: no new designs

Reason: other non-registered pages need to be re-designed

```html
<!DOCTYPE html>
<html lang="zh">
<head>
<meta charset="utf-8">
<title>Kelumo.cn 保障介绍</title>
<link href="https://fonts.googleapis.com/css2?family=Noto+Sans+SC:wght@400;500;700&display=swap" rel="stylesheet">
<style>
:root{
  --bg:#f8f8f8;
  --blue:#1f9ad8;
  --green:#5fba2c;
  --ink:#2b2b2b;
  --muted:#8c8c8c;
  --rule:#d9d9d9;
  --icon-grey:#7d7d7d;
}
*{margin:0;padding:0;box-sizing:border-box}
html,body{width:1146px;height:1200px;overflow:hidden;background:var(--bg)}
body{font-family:"Noto Sans SC",sans-serif;color:var(--ink);position:relative}
.divider{position:absolute;left:559px;top:38px;width:1px;height:1110px;background:#e6e6e6}
.block{position:absolute;width:415px}
.block-head{position:relative;height:56px}
.block-head svg{position:absolute;left:0;top:0}
.block-title{position:absolute;left:38px;top:12px;font-size:23px;font-weight:400;color:var(--ink)}
.block-rule{position:absolute;left:0;top:52px;width:415px;height:1px;background:var(--rule)}
.block-rule::before{content:"";position:absolute;left:0;top:-1px;width:157px;height:3px;background:var(--blue)}
.subtitle{position:absolute;font-size:15px;font-weight:500;color:var(--ink)}
.copy{position:absolute;font-size:13px;line-height:23px;color:var(--muted)}
.copy.tight{font-size:12.5px;line-height:17.2px}
.figure{position:absolute}
.rates{position:absolute;left:0;width:415px;border-collapse:collapse;font-size:12.5px;color:var(--muted)}
.rates th{font-weight:400;color:var(--ink);height:30px;border-bottom:2px solid var(--green);text-align:center}
.rates td{height:24px;text-align:center}
.rates .brand-cell{width:58px;border-right:2px solid var(--green);color:var(--green);font-size:11px}
.policy-link{position:absolute;left:162px;font-size:13px;color:var(--green);text-decoration:underline}
.host{position:absolute;left:220px;width:200px;text-align:center}
.host-name{font-size:15px;font-weight:500;color:var(--ink)}
.host-label{font-size:14px;color:var(--ink);margin-top:10px}
.pay{font-size:15px;font-weight:500;color:var(--ink);margin-top:8px}
</style>
</head>
<body>
<div class="divider"></div>

<section class="block" style="left:118px;top:38px">
  <div class="block-head">
    <svg width="30" height="40" viewBox="0 0 30 40" fill="none" stroke="var(--blue)" stroke-width="2"><rect x="2" y="5" width="24" height="32" rx="3"/><rect x="9" y="1" width="10" height="7" rx="2"/><path d="M7 16l2 2 3-3M15 17h7M7 24l2 2 3-3M15 25h7M7 31h3M15 31h7"/></svg>
    <h2 class="block-title">1, 风控</h2>
    <div class="block-rule"></div>
  </div>
  <h3 class="subtitle" style="left:0;top:78px">樣本標題樣本標題</h3>
  <p class="copy" style="left:0;top:108px;width:200px">坐阿梅特，請與我們聯繫，但一個偉大的想法拉伊德通過某種投資。這就是為什麼人們把一個簡單的例子，其中我們曾經承諾正常的鍛煉，從中獲得了一些優勢，因為他們的榜樣。這是一個痛苦的 美國的艱辛和免疫系統很容易，但下午有現成的導向與義憤文字和信息。</p>
  <svg class="figure" style="left:222px;top:80px" width="180" height="210" viewBox="0 0 180 210" font-size="7" text-anchor="middle" fill="#222">
    <ellipse cx="90" cy="10" rx="88" ry="9" fill="#cdeefb"/>
    <path d="M2 10h176l-14 28H16z" fill="#b4e3f8"/>
    <path d="M16 38h148l-12 26H28z" fill="#93d3f2"/>
    <path d="M28 64h124l-11 26H39z" fill="#6fc0ea"/>
    <path d="M39 90h102l-9 26H48z" fill="#3f9fd8"/>
    <path d="M48 116h84l-7 22H55z" fill="#8ed14a"/>
    <path d="M55 138h70l-5 20H60z" fill="#6dbb2f"/>
    <path d="M60 158h60l-4 20H64z" fill="#4da51f"/>
    <ellipse cx="90" cy="180" rx="26" ry="6" fill="#3d8f17"/>
    <text x="90" y="40">樣本標</text><text x="90" y="72">樣本標</text><text x="90" y="99">標題</text><text x="90" y="125">樣本</text><text x="90" y="148">樣本標</text><text x="90" y="168">樣本標題</text><text x="90" y="187">樣本</text>
  </svg>
</section>

<section class="block" style="left:585px;top:38px">
  <div class="block-head">
    <svg width="38" height="40" viewBox="0 0 38 40" fill="none" stroke="var(--blue)" stroke-width="3"><circle cx="5" cy="22" r="3.5"/><circle cx="33" cy="8" r="3.5"/><circle cx="33" cy="22" r="3.5"/><circle cx="33" cy="36" r="3.5"/><path d="M9 22h20M18 22V8h11M18 22v14h11"/></svg>
    <h2 class="block-title" style="left:48px">2, 分散</h2>
    <div class="block-rule"></div>
  </div>
  <h3 class="subtitle" style="left:0;top:78px">樣本標題樣本標題</h3>
  <p class="copy" style="left:0;top:110px;width:200px;line-height:18px;font-size:12.5px">坐阿梅特，請與我們聯繫，但一個偉大的想法拉伊德通過某種投資。這就是為什麼人們把一個簡單的例子</p>
  <svg class="figure" style="left:0;top:80px" width="415" height="300" viewBox="0 0 415 300">
    <defs><g id="person"><circle cx="0" cy="-14" r="7"/><path d="M-13 0q0-9 13-9t13 9v14h-4v12h-18V14h-4z"/><path d="M0-6l-2 3 2 12 2-12z" fill="#fff"/></g></defs>
    <g stroke="#d4d4d4" fill="none"><path d="M68 152h270M253 29v241M253 29h85M253 88h85M253 150h85M253 212h85M253 270h85"/></g>
    <g fill="var(--icon-grey)">
      <use href="#person" x="28" y="146"/>
      <use href="#person" x="352" y="28"/>
      <use href="#person" x="352" y="87"/>
      <use href="#person" x="352" y="149"/>
      <use href="#person" x="352" y="211"/>
      <use href="#person" x="352" y="270"/>
    </g>
    <text x="28" y="182" font-size="12" fill="#555" text-anchor="middle">示例文本</text>
    <text x="28" y="200" font-size="12" fill="var(--blue)" text-anchor="middle">￥1000</text>
    <g font-size="13" fill="var(--blue)">
      <text x="372" y="32">￥200</text><text x="372" y="91">￥200</text><text x="372" y="153">￥200</text><text x="372" y="215">￥200</text><text x="372" y="274">￥200</text>
    </g>
  </svg>
</section>

<section class="block" style="left:118px;top:438px;height:370px">
  <div class="block-head">
    <svg width="40" height="40" viewBox="0 0 40 40" fill="var(--blue)"><rect x="1" y="20" width="18" height="4"/><rect x="1" y="26" width="18" height="4"/><rect x="1" y="32" width="18" height="4"/><rect x="8" y="4" width="16" height="4"/><rect x="8" y="10" width="16" height="4"/><circle cx="29" cy="26" r="10" fill="none" stroke="var(--blue)" stroke-width="2.5"/><text x="29" y="31" font-size="13" text-anchor="middle" font-weight="700">$</text></svg>
    <h2 class="block-title" style="left:48px">3, 保护金</h2>
    <div class="block-rule"></div>
  </div>
  <h3 class="subtitle" style="left:0;top:78px">標題範例</h3>
  <p class="copy" style="left:0;top:106px;width:225px">将您的资金投资到多个借款人，以进一步降低您的投资风险。Kelumo的规则旨在确保每个借款人必须拥有多名出借人。请尝试使用快速投资功能</p>
  <svg class="figure" style="left:222px;top:68px" width="200" height="140" viewBox="0 0 200 140" font-size="9">
    <circle cx="92" cy="74" r="60" fill="var(--green)"/>
    <path d="M92 14a60 60 0 0 1 50 93L92 74z" fill="var(--blue)" transform="rotate(20 92 74)"/>
    <circle cx="92" cy="74" r="46" fill="#2aa6df"/>
    <circle cx="92" cy="74" r="34" fill="#111"/>
    <circle cx="92" cy="74" r="24" fill="var(--green)"/>
    <text x="92" y="78" text-anchor="middle" fill="#fff" font-size="10">Kelumo</text>
    <path d="M48 21l-6-10H8" stroke="var(--green)" fill="none"/><circle cx="48" cy="21" r="2" fill="var(--green)"/>
    <text x="8" y="9" fill="var(--green)">示例文本</text>
    <path d="M110 54l20-41h4" stroke="#111" fill="none"/><circle cx="130" cy="13" r="2" fill="#111"/>
    <text x="136" y="15" fill="#111">示例文本</text>
    <path d="M136 48l16-8h24" stroke="var(--blue)" fill="none"/><circle cx="136" cy="48" r="2" fill="var(--blue)"/>
    <text x="157" y="38" fill="var(--blue)">示例文本</text>
  </svg>
  <table class="rates" style="top:212px">
    <tr><th class="brand-cell"></th><th>示例文本</th><th>示例文本示例</th><th>示例文本</th><th>示例文本</th></tr>
    <tr><td class="brand-cell" rowspan="3"><svg width="28" height="28"><circle cx="14" cy="14" r="13" fill="var(--green)"/></svg><br>kelumo.cn</td><td>1-9月</td><td>100% 示例文本</td><td>示</td><td>示例文本示例</td></tr>
    <tr><td>10-30月</td><td>100% 示例文本</td><td>示例文本示例</td><td>示例文本示例</td></tr>
    <tr><td>10-30月</td><td>100% 示例文本</td><td>示例文本</td><td></td></tr>
  </table>
  <a class="policy-link" style="top:342px">了解风险金政策</a>
</section>

<section class="block" style="left:585px;top:438px">
  <div class="block-head">
    <svg width="36" height="40" viewBox="0 0 36 40"><path d="M3 6q15-6 30 0v12q0 14-15 20Q3 32 3 18z" fill="#222"/><path d="M7 10h11v12H7z" fill="#3aa64a"/><path d="M18 22h11q-3 9-11 12z" fill="#6a2c8a"/><path d="M7 22h11v12q-9-4-11-12z" fill="#fff"/><path d="M18 10h11v12H18z" fill="#fff"/></svg>
    <h2 class="block-title" style="left:48px">4, 将您的风险</h2>
    <div class="block-rule"></div>
  </div>
  <h3 class="subtitle" style="left:0;top:78px">年示例文本每年示例文本</h3>
  <svg class="figure" style="left:0;top:150px" width="415" height="230" viewBox="0 0 415 230" font-size="9" fill="#333">
    <defs>
      <marker id="ah" markerWidth="8" markerHeight="8" refX="7" refY="4" orient="auto"><path d="M0 0l8 4-8 4z" fill="#bbb"/></marker>
      <g id="p2"><circle cx="0" cy="-12" r="6"/><path d="M-11 0q0-8 11-8t11 8v12h-3v8h-16v-8h-3z"/></g>
    </defs>
    <g stroke="#c9c9c9" stroke-width="1.3" fill="none" marker-end="url(#ah)">
      <path d="M318 32H80"/><path d="M62 45l110 50"/><path d="M172 100L62 52"/>
      <path d="M345 45l-110 52"/><path d="M62 190l110-52"/><path d="M176 132L66 184"/>
      <path d="M235 135l112 55"/><path d="M350 180L240 128"/><path d="M345 210H82"/>
    </g>
    <g fill="var(--green)"><rect x="12" y="28" width="16" height="3"/><rect x="12" y="33" width="16" height="3"/><rect x="12" y="38" width="16" height="3"/><rect x="16" y="22" width="14" height="3"/></g>
    <circle cx="31" cy="44" r="8" fill="none" stroke="var(--green)" stroke-width="2"/>
    <text x="6" y="66">示例文本</text>
    <text x="328" y="28" font-size="10" fill="#555">华荣人寿</text>
    <text x="328" y="41" font-size="10" fill="#555">+ Tessmar</text>
    <circle cx="205" cy="78" r="20" fill="var(--green)"/>
    <text x="205" y="81" text-anchor="middle" fill="#fff">Kelumo</text>
    <text x="205" y="110" text-anchor="middle" font-size="8">资金托管账户</text>
    <text x="205" y="124" text-anchor="middle" font-size="10" fill="#555">云钱袋</text>
    <text x="205" y="140" text-anchor="middle" font-size="10" fill="#555">汇通宝</text>
    <text x="205" y="156" text-anchor="middle" font-size="10" fill="#555">信付通</text>
    <text x="78" y="95">示例文本</text><text x="270" y="95">示例文本</text>
    <text x="88" y="160">示例</text><text x="302" y="152">示例文本</text><text x="270" y="187">示例</text>
    <use href="#p2" x="25" y="190" fill="var(--icon-grey)"/><text x="6" y="222">示例文本</text>
    <use href="#p2" x="381" y="190" fill="var(--icon-grey)"/><text x="362" y="222">示例文本</text>
    <text x="175" y="224">示例文本10%</text>
  </svg>
</section>

<section class="block" style="left:118px;top:854px">
  <div class="block-head">
    <svg width="38" height="40" viewBox="0 0 38 40" fill="var(--blue)"><circle cx="30" cy="7" r="6"/><circle cx="7" cy="20" r="6"/><circle cx="30" cy="33" r="6"/><path d="M7 20L30 7M7 20l23 13" stroke="var(--blue)" stroke-width="3"/></svg>
    <h2 class="block-title" style="left:48px">5, 资金安全</h2>
    <div class="block-rule"></div>
  </div>
  <h3 class="subtitle" style="left:0;top:80px">资金安全</h3>
  <p class="copy tight" style="left:0;top:108px;width:220px">您的资金存放在受限制（代管）的第三方支付账户，Kelumo会每月定期对这些账户进行审计。Kelumo与获得正式认可的部门共享信用数据，以帮助建立一个和谐的信用社会。我们的服务器托管于硅谷的顶级行业专家，以确保数据的安全性，加强隐私保护。</p>
  <svg class="figure" style="left:238px;top:78px" width="180" height="180" viewBox="0 0 180 180" font-size="8.5" fill="var(--blue)">
    <circle cx="96" cy="9" r="6" fill="var(--icon-grey)"/><path d="M85 28q0-10 11-10t11 10v10H85z" fill="var(--icon-grey)"/>
    <g stroke="#999" fill="none" stroke-width="1.2"><path d="M85 44v24M81 63l4 6 4-6M106 44v86M102 125l4 6 4-6M85 102v20M81 117l4 6 4-6M145 132h24M165 129l4 3-4 3M145 146h24M165 143l4 3-4 3M145 162h24M165 159l4 3-4 3"/></g>
    <circle cx="85" cy="87" r="13" fill="var(--green)"/>
    <text x="14" y="37">1, 示例文本</text><text x="132" y="74">2, 示例文本</text><text x="3" y="118">2, 示例文本</text>
    <text x="93" y="150" text-anchor="middle" fill="var(--ink)" font-size="11" font-weight="500">安和信联</text>
    <text x="93" y="168" text-anchor="middle" font-size="7" fill="#555">申城信息服务公司</text>
  </svg>
</section>

<section class="block" style="left:585px;top:854px">
  <div class="block-head">
    <svg width="38" height="40" viewBox="0 0 38 40" fill="var(--blue)"><ellipse cx="16" cy="8" rx="15" ry="6"/><path d="M1 12q15 8 30 0v7q-15 8-30 0zM1 23q15 8 30 0v7q-15 8-30 0z"/><path d="M27 20l9 3v7q0 6-9 9-9-3-9-9v-7z" stroke="var(--bg)" stroke-width="2"/></svg>
    <h2 class="block-title" style="left:48px">6, 将您的风险</h2>
    <div class="block-rule"></div>
  </div>
  <h3 class="subtitle" style="left:0;top:80px">资金安全</h3>
  <p class="copy tight" style="left:0;top:108px;width:205px">您的资金存放在受限制（代管）的第三方支付账户，Kelumo会每月定期对这些账户进行审计。Kelumo与获得正式认可的部门共享信用数据，以帮助建立一个和谐的信用社会。我们的服务器托管于硅谷的顶级行业专家，以确保数据的安全性，加强隐私保护。</p>
  <div class="host" style="top:92px">
    <div class="host-name">Norvane Cloud</div>
    <div class="host-label">资金托管账户</div>
    <div class="pay">云钱袋</div>
    <div class="pay">汇通宝</div>
    <div class="pay">信付通</div>
  </div>
</section>
</body>
</html>
```